Home Remodeling company needs a business card design

we need a business card design for home remodeling company in hamilton county, indiana USA. we offers a wide range of construction services including whole house renovations, Design and Build Basements and Kitchen and Bathroom Remodeling . we would like to see designs for both site of business card that use the same color of the company logo and also including all information below :
1- Karim Feltous CEO / General Contractor
2- all company contacts Telephone numbers ( 1-888-DULOM-47 ) ( 317-555-0193) email address ( info@dulomhome.com) website ( www.dulomhome.com ) and social media logos (Facebook- twitter- google plus )
3- company logo
4- licensed . insured . bonded

```html
<!DOCTYPE html>
<html lang="en">
<head>
<meta charset="utf-8">
<title>Dulom Home Remodeling – Business Card</title>
<link rel="stylesheet" href="https://fonts.googleapis.com/css2?family=Roboto:wght@400;500;700;900&display=swap">
<style>
  :root {
    --backdrop: #2e2724;
    --card: #3a3a3b;
    --white: #f2f2f2;
    --soft: #d9d9d9;
    --red: #d3231f;
  }
  * { margin: 0; padding: 0; box-sizing: border-box; }
  html, body { width: 1200px; height: 716px; overflow: hidden; background: var(--backdrop); }
  body { font-family: "Roboto", Arial, sans-serif; color: var(--white); }
  .sheet {
    width: 1200px; height: 716px;
    display: flex; align-items: center; justify-content: center; gap: 40px;
  }
  .card {
    width: 540px; height: 310px;
    background: var(--card);
    position: relative;
    box-shadow: 0 10px 24px rgba(0,0,0,.45);
  }
  /* brand lockup */
  .brand { display: inline-flex; flex-direction: column; }
  .brand-row { display: flex; align-items: center; gap: 8px; }
  .brand-square { width: 14px; height: 14px; background: var(--red); }
  .brand-name {
    font-weight: 900; font-size: 58px; letter-spacing: 4px; line-height: 1;
    color: var(--white);
  }
  .brand-tagline {
    font-weight: 500; font-size: 15px; letter-spacing: 6.4px;
    color: var(--white); margin-top: 6px; margin-left: 22px;
  }
  .card-front { display: flex; align-items: center; justify-content: center; }
  .card-back .brand { position: absolute; left: 34px; top: 64px; }
  .card-back .brand-name { font-size: 44px; letter-spacing: 3px; }
  .card-back .brand-tagline { font-size: 11.5px; letter-spacing: 4.8px; margin-left: 22px; }
  .details { position: absolute; left: 300px; top: 118px; width: 220px; }
  .person-name { color: var(--red); font-weight: 700; font-size: 19px; letter-spacing: .5px; }
  .person-title { font-size: 11.5px; color: var(--soft); margin-top: 2px; }
  .contacts { list-style: none; margin-top: 12px; }
  .contacts li { display: flex; align-items: center; gap: 9px; font-size: 13px; line-height: 18px; }
  .contacts svg { width: 10px; height: 10px; flex: none; }
  .social { display: flex; align-items: center; gap: 5px; margin-top: 10px; }
  .social-label { color: var(--red); font-size: 12.5px; margin-right: 4px; }
  .social-box { width: 15px; height: 15px; background: var(--white); border-radius: 2px; }
  .credentials { position: absolute; left: 300px; bottom: 22px; font-size: 14px; word-spacing: 2px; }
</style>
</head>
<body>
<main class="sheet">
  <section class="card card-front" aria-label="Card front">
    <div class="brand">
      <div class="brand-row">
        <span class="brand-square"></span>
        <span class="brand-name">DULOM</span>
      </div>
      <span class="brand-tagline">HOME REMODELING</span>
    </div>
  </section>

  <section class="card card-back" aria-label="Card back">
    <div class="brand">
      <div class="brand-row">
        <span class="brand-square"></span>
        <span class="brand-name">DULOM</span>
      </div>
      <span class="brand-tagline">HOME REMODELING</span>
    </div>

    <div class="details">
      <p class="person-name">Karim Feltous</p>
      <p class="person-title">CEO / General Contractor</p>
      <ul class="contacts">
        <li><svg viewBox="0 0 10 10"><path fill="#d3231f" d="M2 0.5 L3.6 2.6 L2.8 3.6 Q3.8 5.8 6.2 7 L7.2 6.2 L9.4 7.8 L8.2 9.5 Q3.5 9 0.5 1.8 Z"/></svg>1-888-DULOM-47</li>
        <li><svg viewBox="0 0 10 10"><path fill="#d3231f" d="M2 0.5 L3.6 2.6 L2.8 3.6 Q3.8 5.8 6.2 7 L7.2 6.2 L9.4 7.8 L8.2 9.5 Q3.5 9 0.5 1.8 Z"/></svg>317-555-0193</li>
        <li><svg viewBox="0 0 10 10"><rect x="0.5" y="2" width="9" height="6.5" fill="#d3231f"/><path d="M0.8 2.4 L5 5.6 L9.2 2.4" fill="none" stroke="#3a3a3b" stroke-width="0.9"/></svg>info@dulomhome.com</li>
        <li><svg viewBox="0 0 10 10"><circle cx="5" cy="5" r="4.3" fill="none" stroke="#d3231f" stroke-width="1.2"/><ellipse cx="5" cy="5" rx="1.8" ry="4.3" fill="none" stroke="#d3231f" stroke-width="0.9"/><line x1="0.7" y1="5" x2="9.3" y2="5" stroke="#d3231f" stroke-width="0.9"/></svg>www.dulomhome.com</li>
      </ul>
      <div class="social">
        <span class="social-label">Follows on:</span>
        <span class="social-box"></span>
        <span class="social-box"></span>
        <span class="social-box"></span>
      </div>
    </div>

    <p class="credentials">Licensed &bull; Insured &bull; Bonded</p>
  </section>
</main>
</body>
</html>
```